Re-design and craft the perfect CV platform

We are building a CV-based platform designed to connect employees and employers, with a strong focus on individual users. As we're just starting out, we're looking to have our platform and logo redesigned to better reflect our vision
https://app.zelvorhire.com/
Colors like in the logo attached
#87C032 #6A6E71 #618930 - also you can add more colors if you like.
https://app.zelvorhire.com/dashboard - This page would be nice if you plan it, like personal Bio dashboard. Attached picture (Dashboard wanted) one idea from how we would like to be, but we are open for new professional ideas/solutions.
https://app.zelvorhire.com/posts - On this page we want to be showed the jobs posted. Attached one picture about our idea (jobs page wanted)
https://app.zelvorhire.com/profile - design something nice.
Only Photoshop, Illustrator or Figma
Other pictures from the app attached (as looking right now)

Target Market(s)

Job seekers, HR, Recruiters

Industry/Entity Type

HR Tech

Number of Pages Required

5+ page

Colors
00AB8E
00BBA5
67D7C9
C6EFE9
E9F9F6

```html
<!DOCTYPE html>
<html lang="en">
<head>
<meta charset="utf-8">
<title>Zelvorhire – Recruitment Web App Access</title>
<link href="https://fonts.googleapis.com/css2?family=Poppins:wght@400;500;600;700&display=swap" rel="stylesheet">
<style>
  :root {
    --brand-green: #87C032;
    --brand-green-dark: #618930;
    --brand-gray: #6A6E71;
    --text-soft: #7a7d80;
    --bg-light: #ececec;
    --bg-mid: #e2e2e2;
    --card-bg: #ffffff;
    --field-bg: #efeff0;
    --rule: #e4e4e4;
  }
  * { box-sizing: border-box; margin: 0; padding: 0; }
  html, body { width: 1200px; height: 712px; overflow: hidden; }
  body {
    font-family: "Poppins", sans-serif;
    background: radial-gradient(ellipse at 40% 35%, #f1f1f1 0%, var(--bg-light) 55%, var(--bg-mid) 100%);
    position: relative;
    color: var(--brand-gray);
  }
  .brand {
    position: absolute;
    left: 200px; top: 72px; width: 250px;
    display: flex; flex-direction: column; align-items: center; gap: 14px;
  }
  .brand-dot {
    width: 58px; height: 58px; border-radius: 50%;
    background: var(--brand-green);
  }
  .brand-name {
    font-size: 34px; font-weight: 600; letter-spacing: 0.5px;
    color: var(--brand-green); line-height: 1;
  }
  .login-card {
    position: absolute;
    left: 140px; top: 216px; width: 371px; height: 379px;
    background: var(--card-bg);
    border-radius: 30px;
    border: 1px solid #e6e6e6;
    box-shadow: 0 30px 40px -18px rgba(0,0,0,0.18);
  }
  .card-title {
    position: absolute; left: 32px; top: 22px;
    font-size: 19.5px; font-weight: 600; color: var(--brand-gray);
    white-space: nowrap;
  }
  .card-title .accent { color: var(--brand-green); }
  .card-rule {
    position: absolute; left: 28px; top: 69px; width: 314px;
    height: 1px; background: var(--rule);
  }
  .login-heading {
    position: absolute; left: 32px; top: 105px;
    font-size: 16px; font-weight: 500; color: var(--brand-gray);
  }
  .login-intro {
    position: absolute; left: 32px; top: 139px; width: 320px;
    font-size: 11.4px; line-height: 17px; color: var(--text-soft);
  }
  .field-label {
    position: absolute; left: 33px; top: 203px;
    font-size: 10.5px; font-weight: 600; color: var(--brand-gray);
  }
  .field-label .required { color: var(--brand-green); }
  .email-field {
    position: absolute; left: 33px; top: 226px; width: 305px; height: 44px;
    background: var(--field-bg); border-radius: 22px;
    display: flex; align-items: center; padding-left: 21px; gap: 10px;
    font-size: 11px; color: var(--text-soft);
  }
  .continue-button {
    position: absolute; left: 33px; top: 287px; width: 305px; height: 45px;
    background: var(--brand-green); border-radius: 23px;
    display: flex; align-items: center; justify-content: center;
    font-size: 12px; font-weight: 700; color: #fff; letter-spacing: 0.2px;
  }
  .continue-arrow {
    position: absolute; right: 7px; top: 6px;
    width: 33px; height: 33px; border-radius: 50%; background: #fff;
    display: flex; align-items: center; justify-content: center;
  }
  .hero-photo {
    position: absolute; left: 612px; top: 72px; width: 512px; height: 640px;
    border-radius: 180px 180px 0 0;
    background: linear-gradient(180deg, #c9d3dc 0%, #8ea4ba 45%, #6f8aa6 75%, #7fae3d 100%);
    opacity: 0.9;
  }
</style>
</head>
<body>
  <header class="brand">
    <div class="brand-dot"></div>
    <div class="brand-name">ZELVORHIRE</div>
  </header>

  <main class="login-card">
    <h1 class="card-title">Recruitment <span class="accent">Web App</span> Access</h1>
    <div class="card-rule"></div>
    <h2 class="login-heading">Log in to your account</h2>
    <p class="login-intro">Welcome to Zelvor Hire, please put your login credentials below to start using the app</p>
    <div class="field-label">Email Address<span class="required">*</span></div>
    <div class="email-field">
      <svg width="12" height="10" viewBox="0 0 12 10" aria-hidden="true">
        <rect x="0" y="1" width="12" height="8" rx="1.2" fill="#6A6E71"/>
        <path d="M0.6 1.6 L6 5.4 L11.4 1.6" fill="none" stroke="#efeff0" stroke-width="1.1"/>
      </svg>
      <span>Enter email address</span>
    </div>
    <div class="continue-button">
      CONTINUE
      <span class="continue-arrow">
        <svg width="8" height="9" viewBox="0 0 8 9" aria-hidden="true">
          <path d="M2.5 1.5 L5.5 4.5 L2.5 7.5" fill="none" stroke="#6A6E71" stroke-width="1.4" stroke-linecap="round" stroke-linejoin="round"/>
        </svg>
      </span>
    </div>
  </main>

  <div class="hero-photo" role="img" aria-label="Photo of a young man in a denim jacket sitting on a green block with a laptop"></div>
</body>
</html>
```